Promotional brochure for educational consulting firm

Updates

Hi Designers!

Please do a 8.5 x 11 inch tri-fold brochure as well as a 8.5 x 11 inch half-fold brochure.  I appreciate black and white versions in addition to color.  Please take a look at my company's website for a better sense of the look and feel I am going for:  www.brightlanepa.org

Thanks!

Industry/Entity Type

Consulting

Colors
3176b5
85abd2
fcfbfd

```html
<!DOCTYPE html>
<html lang="en">
<head>
<meta charset="utf-8">
<title>Brightlane Associates – Brochures</title>
<link rel="stylesheet" href="https://fonts.googleapis.com/css2?family=Tinos:ital,wght@0,400;0,700;1,400;1,700&family=Open+Sans:wght@400;600;700&display=swap">
<style>
  :root{
    --blue:#3176b5;
    --sky:#85abd2;
    --paper:#fcfbfd;
    --deep:#2a5ca6;
    --ink:#4d4f55;
    --stage:#e6e6e8;
    --fold:#eef0f5;
    --serif:"Tinos", "Times New Roman", serif;
    --sans:"Open Sans", Arial, sans-serif;
  }
  *{box-sizing:border-box;margin:0;padding:0}
  html,body{width:1200px;height:970px;overflow:hidden}
  body{background:var(--stage);position:relative;font-family:var(--serif);color:var(--ink)}

  /* ---------- Tri-fold inside spread ---------- */
  .trifold{position:absolute;left:300px;top:12px;width:860px;height:460px;
    display:grid;grid-template-columns:repeat(3,1fr);overflow:hidden;
    background:var(--paper);box-shadow:0 4px 14px rgba(0,0,0,.18)}
  .trifold .panel{position:relative;padding:22px 20px 0;z-index:1}
  .trifold .panel--middle{background:var(--fold)}
  .trifold .wave{position:absolute;left:0;bottom:0;width:100%;height:100px;z-index:0}
  .intro{font-size:12px;line-height:1.35}
  .intro .brand-word{color:var(--blue);font-size:15px}
  .intro p+p{margin-top:12px}
  .illustration{margin-top:22px;width:150px;height:140px;border-radius:4px;
    background:linear-gradient(160deg,#8fd06a 0%,#e8e04a 45%,#e45a3a 80%,#f1f1f3 100%)}
  .panel-brand{position:absolute;left:20px;bottom:22px;display:flex;align-items:center;gap:8px;z-index:2}
  .dot{width:26px;height:26px;border-radius:50%;background:#fff;flex:none}
  .panel-brand .name{font-family:var(--serif);font-size:11px;color:#fff;line-height:1.2}
  .panel-brand .tag{font-size:7px;letter-spacing:.4px;color:#fff}

  .question-icon{width:44px;height:48px;margin:0 auto 12px;border-radius:4px;
    background:linear-gradient(135deg,#dfe9f6,#aac4e3)}
  .questions{list-style:none;font-size:10.5px;color:var(--deep);line-height:1.3}
  .questions li{margin-bottom:8px}
  .questions strong{font-size:13px;font-weight:700}
  .closing{font-style:italic;font-weight:700;font-size:12px;color:var(--deep);line-height:1.3;margin-top:4px}
  .web{position:absolute;bottom:14px;left:0;right:0;text-align:center;
    font-style:italic;font-size:12px;color:#fff;z-index:2}

  .founder{display:flex;justify-content:center;align-items:flex-start;gap:8px}
  .portrait{width:44px;height:54px;background:linear-gradient(180deg,#b9b3ad,#6b5f58)}
  .founder-caption{font-style:italic;font-size:9px;line-height:1.3;margin-top:8px}
  .bio{font-size:11px;line-height:1.35;margin-top:12px}
  .bio strong{color:var(--blue)}
  .expertise-title{font-weight:700;color:var(--deep);font-size:11px;margin:12px 0 8px}
  .expertise{list-style:none;font-size:10px;line-height:1}
  .expertise li{display:flex;align-items:center;gap:6px;margin-bottom:9px}
  .tick{width:8px;height:8px;flex:none}
  .contact-lines{position:absolute;right:40px;bottom:14px;font-size:12px;color:#fff;line-height:1.3;z-index:2}

  /* ---------- Half-fold spread ---------- */
  .halffold{position:absolute;left:40px;top:490px;width:860px;height:460px;
    display:grid;grid-template-columns:repeat(3,1fr);background:var(--paper);
    box-shadow:0 4px 14px rgba(0,0,0,.18);overflow:hidden}
  .halffold .panel{position:relative;overflow:hidden}
  .panel--inside{background:linear-gradient(90deg,#f4f5f8,var(--paper))}
  .motto{position:absolute;left:30px;right:30px;top:140px;font-family:var(--sans);color:var(--blue)}
  .motto .rule{height:1px;background:var(--blue);margin:0 10px}
  .motto .lead{font-size:13px;text-align:center;margin:18px 0 2px;color:#333}
  .motto .big{font-size:30px;text-align:center;margin-bottom:20px}

  .panel--back{font-family:var(--sans)}
  .back-band{position:absolute;top:0;left:0;width:100%;height:105px}
  .back-brand{position:absolute;top:34px;left:0;right:0;text-align:center;color:#fff;z-index:1}
  .back-brand .name{font-size:13px;font-weight:600}
  .back-brand .tag{font-size:7px;letter-spacing:.5px}
  .contact{position:absolute;top:118px;left:34px;right:24px;font-size:10px;color:#333;line-height:1.45}
  .contact h2{font-size:14px;font-weight:700;margin:12px 0 6px 60px}
  .contact .person{font-weight:700}
  .class-photo{position:absolute;left:40px;top:300px;width:200px;height:100px;border:3px solid #fff;
    box-shadow:0 1px 4px rgba(0,0,0,.25);background:linear-gradient(135deg,#e7c98e,#a9c3df 60%,#dcdde2)}
  .foot-brand{position:absolute;left:40px;bottom:18px;display:flex;align-items:center;gap:8px;color:var(--blue)}
  .foot-brand .dot{background:var(--blue);width:20px;height:20px}
  .foot-brand .name{font-size:10px;font-weight:600}
  .foot-brand .tag{font-size:6px;letter-spacing:.4px}

  .cover-photo{position:absolute;left:0;top:0;width:100%;height:330px;
    background:linear-gradient(170deg,#2f3a3c 0%,#3d4a4c 40%,#c94a3a 70%,#e08a3a 100%)}
  .cover-band{position:absolute;left:0;bottom:0;width:100%;height:170px}
  .cover-brand{position:absolute;left:0;right:0;bottom:40px;text-align:center;color:#fff;font-family:var(--sans)}
  .cover-brand .dot{margin:0 auto 10px;width:36px;height:36px}
  .cover-brand .name{font-size:15px;font-weight:600}
  .cover-brand .tag{font-size:8px;letter-spacing:.6px}
</style>
</head>
<body>

<section class="trifold" aria-label="Tri-fold brochure, inside">
  <svg class="wave" viewBox="0 0 860 100" preserveAspectRatio="none" aria-hidden="true">
    <path d="M0 25 C220 0 430 70 860 20 L860 100 L0 100Z" fill="#85abd2" opacity=".45"/>
    <path d="M0 50 C240 30 470 85 860 40 L860 100 L0 100Z" fill="#3176b5"/>
  </svg>

  <div class="panel panel--left">
    <div class="intro">
      <p><span class="brand-word">Brightlane Associates</span> provides just-in-time support to schools and school leaders.</p>
      <p>Schools along the continuum of organizational growth—from startup schools to developing or mature schools—can benefit from specialized expertise to complete a time-sensitive special project or develop strategies and processes to take their program to the next level of excellence.</p>
    </div>
    <div class="illustration" role="img" aria-label="Illustration of a figure pushing a rising growth arrow"></div>
    <div class="panel-brand">
      <span class="dot"></span>
      <div><div class="name">Brightlane Associates LLC</div><div class="tag">SUPPORTING SCHOOLS &amp; SCHOOL LEADERS</div></div>
    </div>
  </div>

  <div class="panel panel--middle">
    <div class="question-icon" role="img" aria-label="Illustration of a figure beside a question mark sign"></div>
    <ul class="questions">
      <li>How do I develop a high-functioning <strong>board</strong>?</li>
      <li>What <strong>policies</strong> do start-up schools need to have on day one?</li>
      <li>Is my meal program optimizing <strong>revenue</strong>?</li>
      <li>We want to refinance our property. How do we tell our story to a <strong>lender</strong>?</li>
      <li>How can we increase <strong>parent engagement</strong>?</li>
      <li>What do we need to do to increase visibility (and <strong>enrollment</strong>)?</li>
      <li>My assistant principal is going out on extended leave… can I get someone to <strong>step in</strong> while he's out?</li>
    </ul>
    <p class="closing">Do these questions keep you up at night? If so, we can help</p>
    <div class="web">www.brightlanepa.org</div>
  </div>

  <div class="panel panel--right">
    <div class="founder">
      <div class="portrait" role="img" aria-label="Portrait photo of the founder"></div>
      <div class="founder-caption">Dana Morrow, Ed.D.<br>Founder &amp; CEO</div>
    </div>
    <p class="bio">My 10-year experience as an executive director of charter schools in the two largest school districts in California gives me a unique "<strong>education + business</strong>" perspective in addition to a network of on-call, expert associates who are ready to assist your school in a variety of key areas.</p>
    <p class="expertise-title">Our areas of expertise include:</p>
    <ul class="expertise">
      <li><svg class="tick" viewBox="0 0 10 10"><path d="M1 5 L4 8 L9 1" fill="none" stroke="#333" stroke-width="1.6"/></svg>Board Training</li>
      <li><svg class="tick" viewBox="0 0 10 10"><path d="M1 5 L4 8 L9 1" fill="none" stroke="#333" stroke-width="1.6"/></svg>Budget and Operations</li>
      <li><svg class="tick" viewBox="0 0 10 10"><path d="M1 5 L4 8 L9 1" fill="none" stroke="#333" stroke-width="1.6"/></svg>Charter Development</li>
      <li><svg class="tick" viewBox="0 0 10 10"><path d="M1 5 L4 8 L9 1" fill="none" stroke="#333" stroke-width="1.6"/></svg>Communications</li>
      <li><svg class="tick" viewBox="0 0 10 10"><path d="M1 5 L4 8 L9 1" fill="none" stroke="#333" stroke-width="1.6"/></svg>Leadership Coaching</li>
      <li><svg class="tick" viewBox="0 0 10 10"><path d="M1 5 L4 8 L9 1" fill="none" stroke="#333" stroke-width="1.6"/></svg>Lender Negotiations</li>
      <li><svg class="tick" viewBox="0 0 10 10"><path d="M1 5 L4 8 L9 1" fill="none" stroke="#333" stroke-width="1.6"/></svg>Fund Development</li>
      <li><svg class="tick" viewBox="0 0 10 10"><path d="M1 5 L4 8 L9 1" fill="none" stroke="#333" stroke-width="1.6"/></svg>Placement of interim administrators</li>
    </ul>
    <div class="contact-lines">[t] 555.014.2270<br>[f] 555.014.3381</div>
  </div>
</section>

<section class="halffold" aria-label="Half-fold brochure">
  <div class="panel panel--inside">
    <div class="motto">
      <div class="rule"></div>
      <p class="lead">School leadership is</p>
      <p class="big">24/7/365</p>
      <div class="rule"></div>
    </div>
  </div>

  <div class="panel panel--back">
    <svg class="back-band" viewBox="0 0 287 105" preserveAspectRatio="none" aria-hidden="true">
      <path d="M0 0 H287 V70 C200 100 90 80 0 105Z" fill="#3176b5"/>
    </svg>
    <div class="back-brand">
      <div class="name">Brightlane Associates LLC</div>
      <div class="tag">SUPPORTING SCHOOLS &amp; SCHOOL LEADERS</div>
    </div>
    <div class="contact">
      <p>Let's work together to take your school to the next level of excellence.</p>
      <h2>Contact Us</h2>
      <p class="person">Dana Morrow, Ed.D.</p>
      <p>[t] 555.014.2270<br>[f] 555.014.3381<br>dana@brightlanepa.org<br>www.brightlanepa.org</p>
    </div>
    <div class="class-photo" role="img" aria-label="Photo of students working together at a classroom table"></div>
    <div class="foot-brand">
      <span class="dot"></span>
      <div><div class="name">Brightlane Associates LLC</div><div class="tag">SUPPORTING SCHOOLS &amp; SCHOOL LEADERS</div></div>
    </div>
  </div>

  <div class="panel panel--cover">
    <div class="cover-photo" role="img" aria-label="Photo of students raising their hands in front of a chalkboard"></div>
    <svg class="cover-band" viewBox="0 0 287 170" preserveAspectRatio="none" aria-hidden="true">
      <path d="M0 40 C90 10 200 10 287 45 V170 H0Z" fill="#3176b5"/>
    </svg>
    <div class="cover-brand">
      <div class="dot"></div>
      <div class="name">Brightlane Associates LLC</div>
      <div class="tag">SUPPORTING SCHOOLS &amp; SCHOOL LEADERS</div>
    </div>
  </div>
</section>

</body>
</html>
```